Stationary - Based On Previous Design

Basic stationary with a header and footer

Target Market(s)

Friends, Colleagues, More friendly than professional

Industry/Entity Type

legal/personal

Colors
00AB8E
00BBA5
67D7C9
C6EFE9
E9F9F6

Requirements
Must have
• Green & White
Nice to have
• I like the "G" on the business card and was thinking that would be for both G's in "PellaNote"
Should not have
• other colors

```html
<!DOCTYPE html>
<html lang="en">
<head>
<meta charset="utf-8">
<title>PellaNote Stationery</title>
<link href="https://fonts.googleapis.com/css2?family=Outfit:wght@400;500;600;700&family=Roboto:wght@300;400;500&display=swap" rel="stylesheet">
<style>
  :root {
    --teal: #00bba5;
    --teal-deep: #00ab8e;
    --teal-soft: #67d7c9;
    --mint: #c6efe9;
    --mint-pale: #e9f9f6;
    --ink: #222222;
    --ink-soft: #4a4a4a;
    --grey-text: #5a5a5a;
    --accent-red: #e23b2e;
    --paper: #ffffff;
    --ghost: #f1f1f1;
    --backdrop: #3d3c42;
  }
  * { margin: 0; padding: 0; box-sizing: border-box; }
  html, body { width: 1200px; height: 1054px; overflow: hidden; background: var(--backdrop); }
  .stage { position: relative; width: 1200px; height: 1054px; }

  /* Letterhead */
  .letterhead {
    position: absolute; left: 114px; top: 143px; width: 543px; height: 768px;
    background: var(--paper); overflow: hidden;
    font-family: "Roboto", Arial, sans-serif; color: var(--ink-soft);
  }
  .ghost-circle {
    position: absolute; border-radius: 50%; background: var(--ghost);
  }
  .letterhead .ghost-circle { width: 170px; height: 170px; right: -40px; top: -10px; }
  .brand {
    position: absolute; display: flex; align-items: center; gap: 8px;
    font-family: "Outfit", Arial, sans-serif; font-weight: 700; color: var(--ink-soft);
  }
  .brand-dot { border-radius: 50%; background: var(--teal); flex: none; }
  .letterhead .brand { left: 30px; top: 38px; font-size: 26px; }
  .letterhead .brand-dot { width: 30px; height: 30px; }

  .sender { position: absolute; left: 40px; top: 157px; }
  .sender-name { font-size: 11.5px; font-weight: 500; color: var(--ink); }
  .sender-name .surname { color: var(--accent-red); }
  .sender-role { font-size: 9.5px; font-weight: 400; margin-top: 4px; }
  .contact-list { list-style: none; margin-top: 8px; font-size: 10.5px; font-weight: 300; }
  .contact-list li { line-height: 17px; }
  .contact-list b { font-weight: 500; color: var(--ink); }
  .contact-list b.red { color: var(--accent-red); }
  .letter-date {
    position: absolute; right: 38px; top: 225px; font-size: 10.5px; font-weight: 300;
  }
  .letter-body {
    position: absolute; left: 40px; top: 286px; width: 464px;
    font-size: 10.3px; font-weight: 300; line-height: 18px; text-align: justify;
  }
  .letter-body p + p { margin-top: 18px; }
  .signature {
    position: absolute; left: 40px; top: 630px; width: 92px; height: 24px;
    background: linear-gradient(90deg, var(--mint-pale), var(--ghost));
    border-radius: 4px;
  }
  .signer { position: absolute; left: 40px; top: 660px; }
  .signer-name { font-size: 11.5px; font-weight: 500; color: var(--ink); }
  .signer-role { font-size: 10.5px; font-weight: 300; margin-top: 3px; }

  .letter-footer {
    position: absolute; left: 37px; right: 38px; top: 713px;
    display: flex; justify-content: space-between; align-items: center;
    font-family: "Outfit", Arial, sans-serif; font-size: 9px; color: var(--ink-soft);
  }
  .footer-item { display: flex; align-items: center; gap: 5px; }
  .footer-item.name { font-weight: 600; }
  .icon { width: 14px; height: 14px; flex: none; }
  .footer-item .brand-dot { width: 12px; height: 12px; }

  /* Business cards */
  .card {
    position: absolute; left: 727px; width: 366px; height: 209px; overflow: hidden;
    font-family: "Outfit", Arial, sans-serif;
  }
  .card-front { top: 457px; background: var(--teal); display: flex; align-items: center; justify-content: center; }
  .card-front .brand { position: static; color: var(--paper); font-size: 34px; gap: 12px; }
  .card-front .brand-dot { width: 42px; height: 42px; background: var(--paper); }

  .card-back { top: 702px; background: var(--paper); color: var(--ink-soft); }
  .card-back .ghost-circle { width: 120px; height: 120px; right: -20px; top: 8px; }
  .card-back .brand { left: 26px; top: 30px; font-size: 20px; gap: 7px; }
  .card-back .brand-dot { width: 24px; height: 24px; }
  .holder { position: absolute; left: 27px; top: 95px; }
  .holder-name { font-size: 17.5px; font-weight: 600; color: var(--ink-soft); }
  .holder-role { font-size: 11.5px; font-weight: 400; color: var(--teal); margin-top: 2px; }
  .holder-rule { width: 44px; height: 1px; background: #cfcfcf; margin: 9px 0 9px; }
  .holder-contact { list-style: none; font-size: 11.5px; }
  .holder-contact li { display: flex; align-items: center; gap: 6px; line-height: 19px; }
  .holder-contact .icon { width: 11px; height: 11px; }
</style>
</head>
<body>
<main class="stage">

  <article class="letterhead">
    <div class="ghost-circle"></div>
    <header class="brand"><span class="brand-dot"></span>PellaNote</header>

    <section class="sender">
      <div class="sender-name">Laura <span class="surname">Penn</span></div>
      <div class="sender-role">Designer</div>
      <ul class="contact-list">
        <li><b class="red">A :</b> Your City- Zip Code - 000</li>
        <li><b>W :</b> www.yoursitename.com</li>
        <li><b class="red">P :</b> +000 123 456 789</li>
      </ul>
    </section>
    <div class="letter-date">Date : 25 September, 2030</div>

    <section class="letter-body">
      <p>Lorem ipsum dolor sit amet, consectetur adipisicing elit, sed do eiusmod tempor incididunt ut labore et dolore magna aliqua. Ut enim ad minim veniam, quis nostrud exercitation ullamco laboris nisi ut aliquip ex ea commodo consequat.</p>
      <p>Excepteur sint occaecat cupidatat non proident, sunt in culpa qui officia deserunt mollit anim id est laborum. Sed ut perspiciatis unde omnis iste natus error sit voluptatem accusantium doloremque laudantium, totam rem aperiam, eaque ipsa quae ab illo inventore veritatis et quasi architecto beatae vitae dicta sunt explicabo. Nemo enim ipsam voluptatem quia voluptas sit aspernatur aut odit aut quia consequuntur voluptatem sequi nesciunt.</p>
      <p>Voluptatem accusantium doloremque laudantium, totam rem aperiam, eaque ipsa quae ab illo inventore veritatis et quasi architecto beatae vitae dicta sunt explicabo. Nemo enim ipsam voluptatem quia voluptas sit aspernatur aut odit aut quia consequuntur voluptatem sequi nesciunt.</p>
      <p>Neque porro quisquam dolorem ipsum quia dolor sit amet, consecteturtempora incidunt labore dolore magnam aliquam quaerat voluptatem.</p>
    </section>

    <div class="signature" role="img" aria-label="Handwritten signature of Marcus Reed"></div>
    <section class="signer">
      <div class="signer-name">Marcus Reed</div>
      <div class="signer-role">Manager</div>
    </section>

    <footer class="letter-footer">
      <span class="footer-item name"><span class="brand-dot"></span>Daniel Harlow</span>
      <span class="footer-item">
        <svg class="icon" viewBox="0 0 14 14"><circle cx="7" cy="7" r="7" fill="var(--teal)"/><rect x="3.5" y="4.5" width="7" height="5" rx="0.6" fill="none" stroke="#fff" stroke-width="0.9"/><path d="M3.7 4.8 7 7.4l3.3-2.6" fill="none" stroke="#fff" stroke-width="0.9"/></svg>
        dharlow@harlowlegal.com
      </span>
      <span class="footer-item">
        <svg class="icon" viewBox="0 0 14 14"><circle cx="7" cy="7" r="7" fill="var(--teal)"/><path d="M7 3.2a2.2 2.2 0 0 1 2.2 2.2C9.2 7 7 9.6 7 9.6S4.8 7 4.8 5.4A2.2 2.2 0 0 1 7 3.2z" fill="#fff"/><circle cx="7" cy="5.4" r="0.8" fill="var(--teal)"/><rect x="3.5" y="10" width="7" height="1" rx="0.5" fill="#fff"/></svg>
        418 N Alder Ave Portland, OR 97205
      </span>
    </footer>
  </article>

  <section class="card card-front">
    <div class="brand"><span class="brand-dot"></span>PellaNote</div>
  </section>

  <section class="card card-back">
    <div class="ghost-circle"></div>
    <div class="brand"><span class="brand-dot"></span>PellaNote</div>
    <div class="holder">
      <div class="holder-name">Daniel Harlow</div>
      <div class="holder-role">President</div>
      <div class="holder-rule"></div>
      <ul class="holder-contact">
        <li>
          <svg class="icon" viewBox="0 0 14 14"><circle cx="7" cy="7" r="7" fill="var(--teal)"/><rect x="3.5" y="4.5" width="7" height="5" rx="0.6" fill="none" stroke="#fff" stroke-width="1"/><path d="M3.7 4.8 7 7.4l3.3-2.6" fill="none" stroke="#fff" stroke-width="1"/></svg>
          dharlow@harlowlegal.com
        </li>
        <li>
          <svg class="icon" viewBox="0 0 14 14"><circle cx="7" cy="7" r="7" fill="var(--teal)"/><path d="M7 3.2a2.2 2.2 0 0 1 2.2 2.2C9.2 7 7 9.6 7 9.6S4.8 7 4.8 5.4A2.2 2.2 0 0 1 7 3.2z" fill="#fff"/><circle cx="7" cy="5.4" r="0.8" fill="var(--teal)"/></svg>
          418 N Alder Ave Portland, OR 97205
        </li>
      </ul>
    </div>
  </section>

</main>
</body>
</html>
```